House Cleaning Platform for Consumers and Cleaners

UPDATE: I've attached screenshots showing a purchase flow example, something all designers have missed in their designs. PLEASE check the URLs I've included in the brief for examples of a cleaning website. I've seen mostly landing pages and nothing else.

WHAT I'M LOOKING FOR:
I need the UI designed for a house cleaning web platform from 2 separate experiences: one from the consumer end to order a cleaner to come clean their house and one from a cleaner’s end that manages their orders and manages their schedule.

The UI will need to include photo uploading for before and after photos, a checkout/cart experience w/ tips, toggle options for adding and removing rooms/extras cleaning add-ons, customer+cleaner reviews (meaning the cleaner finished the job and they can rate and review the customer as well as the customer can rate and review the cleaner), order history for consumers, job history for cleaners, profile, settings, and landing pages for both.

PLEASE DO NOT USE THE COLOR BLUE AS THE PRIMARY COLOR. Use a light green (HEX #2fdf86) instead for primary theming color.

REFERENCES:
If you'd like a few websites I've enjoyed for references, checkout:
larkpolish.example, vomby.example, and brightfernhome.example.

For sake of branding, the company name is PlumNest. Currently do not have a logo as we have not decided on the name. Logo will come later.

Feel free to reach out to me if you have any questions!
Updates

Most designer submissions were a landing page and only a landing page. Very few designed the flows I requested and none designed a schedule management page. I even updated the Brief to more clearly outline the needs and references. Only about 2-3 of the designers actually did more than a landing page. Still don't believe I received 6 designers input that I had paid for.

Target Market(s)

FULL-TIME WORKING HOUSEHOLDS, SINGLE PROFESSIONALS, SINGLE PARENTS, ELDERLY & MOBILITY CHALLENGED, BUSY BODIES.

Industry/Entity Type

Cleaning, gig work.

Number of Pages Required

5+ page

Font styles to use
Other font styles liked:
• Jost or Lexend are great Google Font options I've used in the pitch deck and horribly done app mockups.

Colors
00AB8E
00BBA5
67D7C9
C6EFE9
E9F9F6
59FF00
82FF00
B8FF75
E3FFCB
F4FFEA
FFF300
FFF600
FEFA6F
FFFEC7
FFFEE8
FFC000
F8CF3A
FAE287
FDF2CF
FEFAEE

Requirements
Must have
• Landing page, consumer flow, cleaner schedule management, checkout flow, Rate & Review for consumer and/or cleaner, order history, profile.
Nice to have
• I'd like it to be simple in design and modern, but not so simple it's boring. Iconography can sometimes break that up, but I don't want it looking busy. It's a cleaning platform so the UI should look clean.

```html
<!DOCTYPE html>
<html lang="en">
<head>
<meta charset="UTF-8">
<title>PlumNest – Book Your Services</title>
<link href="https://fonts.googleapis.com/css2?family=Nunito:wght@400;500;600&family=Open+Sans:wght@500;600;700&display=swap" rel="stylesheet">
<style>
  :root{
    --green:#2fdf86;
    --green-btn:#27d07f;
    --ink:#111111;
    --text:#333333;
    --muted:#9a9a9a;
    --border:#c9c9c9;
    --secure:#8e8e8e;
    --lock:#e0aa1c;
    --tile:#f3f3f3;
  }
  *{box-sizing:border-box;margin:0;padding:0}
  html,body{width:1200px;height:688px;overflow:hidden;background:#fff}
  body{position:relative;font-family:'Nunito',sans-serif;color:var(--ink)}
  .abs{position:absolute}
  .brand{left:101px;top:18px;font-family:'Open Sans',sans-serif;font-weight:700;font-size:30px;color:var(--green);letter-spacing:-0.5px}
  .nav{top:27px;display:flex;gap:19px;left:438px;font-size:12.5px;font-weight:500}
  .search{left:731px;top:22.5px;width:218px;height:25px;border:1px solid #d6d6d6;border-radius:13px;display:flex;align-items:center;padding-left:7px;font-size:12.5px;font-weight:500}
  .search svg{margin-right:15px}
  .login{left:981px;top:27px;font-size:12.5px;font-weight:500}
  .signup{left:1024px;top:22.5px;width:75px;height:25px;border-radius:13px;background:var(--green-btn);font-size:11px;font-weight:600;display:flex;align-items:center;justify-content:center}
  .title{left:0;width:1160px;top:128px;text-align:center;font-family:'Open Sans',sans-serif;font-weight:700;font-size:38px;letter-spacing:-0.3px}
  .rule{left:0;top:215px;width:1200px;height:1px;background:var(--green)}
  .section-title{left:101px;top:267px;font-family:'Open Sans',sans-serif;font-weight:500;font-size:20px}
  .note{left:101px;top:309px;font-size:11.5px;color:var(--text)}
  .label{left:101px;top:346px;font-family:'Open Sans',sans-serif;font-size:13px}
  .card-field{left:101px;top:377.5px;width:469px;height:37px;border:1px solid var(--border);border-radius:3px;display:flex;align-items:center;padding-left:20px;font-size:11.5px;color:var(--muted)}
  .card-field .num{margin-left:14px;flex:1}
  .card-field .part{padding:0 6px;border-left:1px solid var(--border);line-height:18px}
  .card-field .part:first-of-type{border-left:none}
  .card-field .part:last-child{padding-right:19px}
  .brands{left:101px;top:427.5px;display:flex;gap:5.5px}
  .brands span{width:57.5px;height:35px;background:var(--tile);display:flex;align-items:center;justify-content:center;font-size:10px;font-weight:600;color:#555}
  .lock{left:366px;top:429px}
  .secure{left:402px;top:430px;font-family:Arial,sans-serif;font-weight:700;font-size:13px;line-height:17px;color:var(--secure)}
  .book{left:101px;top:525px;width:175px;height:50px;border-radius:25px;background:var(--green-btn);display:flex;align-items:center;justify-content:center;font-size:15px;font-weight:600}
  .terms{left:101px;top:582px;font-size:11.5px;font-weight:500;color:var(--text)}
</style>
</head>
<body>
  <div class="abs brand">PlumNest</div>
  <nav class="abs nav"><span>Home</span><span>Pricing</span><span>Services</span><span>Contact</span><span>Help</span></nav>
  <div class="abs search">
    <svg width="14" height="14" viewBox="0 0 14 14" fill="none" stroke="#222" stroke-width="1.2"><circle cx="6" cy="6" r="5"/><line x1="9.6" y1="9.6" x2="13" y2="13"/></svg>
    Search
  </div>
  <div class="abs login">Login</div>
  <div class="abs signup">Sign Up</div>

  <h1 class="abs title">Book Your Services Now</h1>
  <div class="abs rule"></div>

  <h2 class="abs section-title">Payment Information</h2>
  <p class="abs note">Your card will not be charged until the day of service.</p>
  <p class="abs label">Credit Card Details</p>

  <div class="abs card-field">
    <svg width="13" height="10" viewBox="0 0 13 10" fill="none" stroke="#e8944a" stroke-width="0.9"><rect x="0.5" y="0.5" width="12" height="9"/><circle cx="3.8" cy="4" r="1.3"/><path d="M2 7.5c0.5-1.3 3-1.3 3.6 0"/><line x1="7" y1="3.5" x2="11" y2="3.5"/><line x1="7" y1="5.5" x2="11" y2="5.5"/></svg>
    <span class="num">Card Number</span>
    <span class="part">MM</span><span class="part">YY</span><span class="part">CC</span>
  </div>

  <div class="abs brands"><span>Corvex</span><span>Pavona</span><span>Tandro</span><span>Meridot</span></div>

  <svg class="abs lock" width="23" height="33" viewBox="0 0 23 33">
    <path d="M5 15V9a6.5 6.5 0 0 1 13 0v6" fill="none" stroke="#8a8a8a" stroke-width="3"/>
    <rect x="1" y="14" width="21" height="19" rx="2" fill="var(--lock)"/>
    <circle cx="11.5" cy="22" r="2.2" fill="#6b4d00"/><rect x="10.6" y="22" width="1.8" height="5" fill="#6b4d00"/>
  </svg>
  <div class="abs secure">SAFE AND SECURE 256-BIT<br>SSL ENCRYPTED PAYMENT</div>

  <div class="abs book">Book Now</div>
  <p class="abs terms">*By clicking confirm booking you are agreeing to our friendly privacy policy and booking terms and conditions.</p>
</body>
</html>
```